Business Card Design for Occupational Medicine Start Up Company

We need to design a professional business card. We are a healthcare company providing occupational medicine services to blue collar industries. We are professional, efficient and high quality service providers.

Target Market(s)

Blue Collar Industry: Shipbuilding, Ports, Trucking Companies; The Executives and Safety Officers for these companies

Industry/Entity Type

Healthcare

Contact Information for Business Card

Logo, Name, Title, Email, Phone

Other font styles liked:
• Please match our Brand Guide

Requirements
Must have
• Our Company Colors and Logo

```html
<!DOCTYPE html>
<html lang="en">
<head>
<meta charset="utf-8">
<title>Harborline Clinics – Business Card</title>
<link href="https://fonts.googleapis.com/css2?family=Montserrat:wght@400;500;700&display=swap" rel="stylesheet">
<style>
  :root {
    --brand-orange: #f5b253;
    --brand-navy: #2b3589;
    --text-gray: #6d6e71;
    --card-white: #ffffff;
    --backdrop: #e4e4e4;
  }
  * { box-sizing: border-box; margin: 0; padding: 0; }
  html, body {
    width: 1200px;
    height: 900px;
    overflow: hidden;
    background: var(--backdrop);
    font-family: "Montserrat", Arial, sans-serif;
  }
  .canvas { position: relative; width: 1200px; height: 900px; }
  .card {
    position: absolute;
    left: 328px;
    width: 445px;
    height: 254px;
    overflow: hidden;
  }
  .card-front { top: 165px; background: var(--card-white); }
  .card-back { top: 467px; background: var(--brand-orange); }

  .front-panel {
    position: absolute;
    left: 0; top: 0;
    width: 171px; height: 100%;
    background: var(--brand-orange);
  }
  .front-panel-tab {
    position: absolute;
    left: 171px; top: 49px;
    width: 2px; height: 156px;
    background: var(--brand-orange);
    border-radius: 0 1px 1px 0;
  }
  .front-mark {
    position: absolute;
    left: 0; top: 0;
    width: 171px; height: 100%;
    display: flex;
    flex-direction: column;
    align-items: center;
    justify-content: center;
    gap: 10px;
  }
  .mark-dot {
    width: 58px; height: 58px;
    border-radius: 50%;
    background: var(--brand-navy);
  }
  .mark-name {
    color: var(--brand-navy);
    font-weight: 700;
    font-size: 12px;
    letter-spacing: 0.06em;
  }

  .contact {
    position: absolute;
    left: 191px;
    top: 84px;
  }
  .contact-name {
    color: var(--brand-navy);
    font-size: 16px;
    font-weight: 400;
    letter-spacing: 0.02em;
    line-height: 1.2;
  }
  .contact-name .given { font-weight: 700; }
  .contact-title {
    color: var(--text-gray);
    font-size: 14px;
    font-weight: 400;
    margin-top: 1px;
    letter-spacing: 0.02em;
  }
  .contact-detail {
    color: var(--text-gray);
    font-size: 12.5px;
    font-weight: 400;
    letter-spacing: 0.02em;
  }
  .contact-email { margin-top: 22px; }
  .contact-phone { margin-top: 8px; }

  .back-mark {
    position: absolute;
    inset: 0;
    display: flex;
    flex-direction: column;
    align-items: center;
    justify-content: center;
    gap: 14px;
  }
  .back-mark .mark-dot { width: 52px; height: 52px; }
  .back-name {
    color: var(--brand-navy);
    font-weight: 700;
    font-size: 22px;
    letter-spacing: 0.04em;
    line-height: 1;
    text-align: center;
  }
</style>
</head>
<body>
<main class="canvas">
  <section class="card card-front" aria-label="Business card front">
    <div class="front-panel"></div>
    <div class="front-panel-tab"></div>
    <div class="front-mark">
      <div class="mark-dot" aria-hidden="true"></div>
      <span class="mark-name">HARBORLINE</span>
    </div>
    <div class="contact">
      <p class="contact-name"><span class="given">DANA</span> HOLLOWAY</p>
      <p class="contact-title">Cardiac Sonographer</p>
      <p class="contact-detail contact-email">dana.holloway@harborlineclinics.com</p>
      <p class="contact-detail contact-phone">555-014-2290</p>
    </div>
  </section>

  <section class="card card-back" aria-label="Business card back">
    <div class="back-mark">
      <div class="mark-dot" aria-hidden="true"></div>
      <p class="back-name">HARBORLINE CLINICS</p>
    </div>
  </section>
</main>
</body>
</html>
```